Velqar Australia Pty Ltd - Stationary design

We need letterheads for hard copy print and e-copy word docs, envelopes - landscape and A3, business cards, With compliment slips and a gloss presentation folder to hold up to 20 A4 pages
Would also like to know what font and size would be recommended to suit our brand.
Logo, Colours, Brand and image can be viewed on www.velqar.com.au

Target Market(s)

Those in pain from 30yrs to 80yrs

Industry/Entity Type

Landscape

Requirements
Must have
• Logo as per trademarked logo on web site
Nice to have
• same colours as our web site logo and design
Should not have
• anything looking cheap or too common
text and font needs to be easy to read but very professional in appearance

```html
<!DOCTYPE html>
<html lang="en">
<head>
<meta charset="utf-8">
<title>Velqar Australia – Envelope</title>
<link href="https://fonts.googleapis.com/css2?family=PT+Sans:wght@400;700&display=swap" rel="stylesheet">
<style>
  :root {
    --frame-grey: #959595;
    --paper: #ffffff;
    --paper-shade: #efefef;
    --brand-navy: #33426b;
    --brand-cyan: #11a9e3;
    --rule-cyan: #2fb4e6;
    --watermark: rgba(51, 66, 107, 0.12);
    --photo-dark: #2e3a58;
    --photo-mid: #6f7f9f;
    --photo-light: #c9cfdc;
  }
  * { margin: 0; padding: 0; box-sizing: border-box; }
  html, body {
    width: 839px; height: 1200px; overflow: hidden;
    background: var(--frame-grey);
    font-family: "PT Sans", Arial, sans-serif;
  }
  .sheet { position: relative; width: 839px; height: 1200px; }

  .envelope {
    position: absolute; left: 17px; width: 805px; overflow: hidden;
    background: linear-gradient(180deg, var(--paper-shade) 0%, var(--paper) 45%, var(--paper) 100%);
  }
  .envelope--front { top: 17px; height: 568px; }
  .envelope--back { top: 609px; height: 575px; }

  /* front */
  .header-rule {
    position: absolute; left: 402px; top: 69px; width: 272px; height: 1.5px;
    background: var(--rule-cyan);
  }
  .brand-name {
    position: absolute; font-weight: 700; color: var(--brand-navy); white-space: nowrap;
  }
  .brand-name--header { left: 680px; top: 61px; font-size: 15px; line-height: 1; }
  .brand-name--watermark {
    left: 40px; top: 250px; font-size: 84px; color: var(--watermark);
    transform: rotate(-52deg); transform-origin: left top;
  }
  .return-address {
    position: absolute; left: 75px; top: 535px;
    font-size: 9.5px; font-weight: 700; color: var(--brand-navy); letter-spacing: 0.2px;
    white-space: nowrap;
  }
  .footer-band { position: absolute; left: 0; top: 553px; height: 15px; }
  .footer-band--cyan { width: 201px; background: var(--brand-cyan); }
  .footer-band--navy { left: 201px; width: 201px; background: var(--brand-navy); }
  .product-photo {
    position: absolute; left: 402px; top: 421px; width: 403px; height: 147px;
    background: linear-gradient(100deg, var(--photo-dark) 0%, var(--photo-mid) 40%, var(--photo-light) 70%, var(--photo-mid) 100%);
  }

  /* back */
  .flap-shape { position: absolute; left: 0; top: 0; }
  .brand-name--flap {
    left: 552px; top: 490px; font-size: 30px; line-height: 1; color: var(--paper);
  }
</style>
</head>
<body>
<main class="sheet">
  <section class="envelope envelope--front" aria-label="Envelope front">
    <div class="brand-name brand-name--watermark" aria-hidden="true">Velqar</div>
    <div class="header-rule"></div>
    <div class="brand-name brand-name--header">Velqar Australia</div>
    <p class="return-address">u4/17 Marlow Street, Carrara QLD 4211, Australia | 1300 482 617</p>
    <div class="footer-band footer-band--cyan"></div>
    <div class="footer-band footer-band--navy"></div>
    <div class="product-photo" role="img" aria-label="Product photo: pain relief device and its box beside a figure with a highlighted spine"></div>
  </section>

  <section class="envelope envelope--back" aria-label="Envelope back">
    <svg class="flap-shape" width="805" height="575" viewBox="0 0 805 575" aria-hidden="true">
      <path d="M402,575 C402,480 460,394 560,394 L805,394 L805,575 Z" fill="var(--brand-navy)"/>
    </svg>
    <div class="brand-name brand-name--flap">Velqar Australia</div>
  </section>
</main>
</body>
</html>
```